New Business card design to reflect rebrand

I would like a business card design with a good base colour for our new logo and also a placeholder for a profile pic of the card holder. the design needs to be editable to the point that we can easily change the picture of the person and use that design for printmerlo etc. we are looking at a metalic finish business card so will need a good base colour to bring out the finish.

Target Market(s)

prospective customers

Industry/Entity Type

Business

Contact Information for Business Card

I would like one editable design that we can change the name of the card holder and profile picture. The design need to be in a format that be send to printmerlo etc.

Our address is Fenwick Lodge, Copse Lane, Ashcombe Vale, GU14 3TP Tel no. 01483 556172

Requirements
Must have
• place holder for a profile pic for the card holder. in AI or preferably PSD format

```html
<!DOCTYPE html>
<html lang="en">
<head>
<meta charset="utf-8">
<title>Corvane Workplace Services – Business Card</title>
<link href="https://fonts.googleapis.com/css2?family=Montserrat:wght@400;500;600;700&display=swap" rel="stylesheet">
<style>
  :root {
    --orange: #ee6524;
    --navy: #2f4a6a;
    --white: #ffffff;
    --stage: #e6e7ea;
    --photo-a: #f08a4e;
    --photo-b: #2b2b33;
  }
  * { box-sizing: border-box; margin: 0; padding: 0; }
  html, body { width: 1200px; height: 900px; overflow: hidden; }
  body {
    background: var(--stage);
    font-family: "Montserrat", Arial, sans-serif;
    position: relative;
  }
  .card {
    position: absolute;
    left: 280px;
    width: 640px;
    height: 366px;
    border-radius: 22px;
    overflow: hidden;
    box-shadow: 0 10px 28px rgba(0,0,0,0.18);
  }
  .card--front { top: 60px; background: var(--orange); }
  .card--back { top: 474px; background: var(--white); }

  /* front */
  .profile-photo {
    position: absolute;
    left: 40px; bottom: 0;
    width: 300px; height: 300px;
    border-radius: 150px 150px 0 0;
    background: linear-gradient(180deg, var(--photo-a) 0%, #b85a3a 45%, var(--photo-b) 100%);
  }
  .front-brand {
    position: absolute;
    left: 360px; top: 92px;
    width: 250px;
    color: var(--white);
  }
  .brand-name {
    display: flex; align-items: center; gap: 10px;
    font-weight: 700; font-size: 40px; letter-spacing: 1px; line-height: 1;
  }
  .brand-dot { width: 16px; height: 16px; border-radius: 50%; background: currentColor; flex: none; }
  .brand-tag {
    font-weight: 700; font-size: 13px; letter-spacing: 3.4px; margin-top: 8px; padding-left: 26px;
  }
  .front-web {
    position: absolute; right: 32px; bottom: 28px;
    color: var(--white); font-size: 17px; font-weight: 500;
  }
  .front-web b { font-weight: 700; }

  /* back */
  .back-brand {
    position: absolute; left: 36px; top: 150px; width: 260px;
    color: var(--navy);
  }
  .back-brand .brand-name { font-size: 38px; }
  .back-brand .brand-tag { font-size: 12.5px; letter-spacing: 3.2px; }
  .divider {
    position: absolute; left: 318px; top: 70px;
    width: 2px; height: 230px;
    background: linear-gradient(180deg, transparent, var(--orange) 20%, var(--orange) 80%, transparent);
  }
  .holder { position: absolute; left: 340px; top: 82px; width: 280px; }
  .holder-name { color: var(--orange); font-weight: 700; font-size: 25px; letter-spacing: 1px; }
  .holder-role { color: var(--navy); font-weight: 700; font-size: 13px; letter-spacing: 1px; margin-top: 2px; }
  .contact-list { list-style: none; margin-top: 22px; color: var(--navy); font-size: 14px; }
  .contact-list li { display: flex; align-items: center; gap: 10px; margin-bottom: 6px; }
  .contact-list svg { width: 13px; height: 13px; flex: none; }
  .contact-list b { color: var(--orange); font-weight: 700; }
  .address { margin-top: 14px; color: var(--navy); font-size: 14px; line-height: 1.45; }
</style>
</head>
<body>

<section class="card card--front">
  <div class="profile-photo" role="img" aria-label="Profile photo of the card holder in a dark suit"></div>
  <div class="front-brand">
    <div class="brand-name"><span class="brand-dot"></span>CORVANE</div>
    <div class="brand-tag">WORKPLACE SERVICES</div>
  </div>
  <div class="front-web">www.<b>corvane</b>.com</div>
</section>

<section class="card card--back">
  <div class="back-brand">
    <div class="brand-name"><span class="brand-dot"></span>CORVANE</div>
    <div class="brand-tag">WORKPLACE SERVICES</div>
  </div>
  <div class="divider"></div>
  <div class="holder">
    <div class="holder-name">MARCUS HALE</div>
    <div class="holder-role">DIRECTOR</div>
    <ul class="contact-list">
      <li>
        <svg viewBox="0 0 24 24" fill="#ee6524"><path d="M6.6 10.8a15.1 15.1 0 0 0 6.6 6.6l2.2-2.2c.3-.3.7-.4 1-.2 1.1.4 2.3.6 3.6.6.6 0 1 .4 1 1V20c0 .6-.4 1-1 1A17 17 0 0 1 3 4c0-.6.4-1 1-1h3.5c.6 0 1 .4 1 1 0 1.3.2 2.5.6 3.6.1.3 0 .7-.2 1z"/></svg>
        <span>01483 556172</span>
      </li>
      <li>
        <svg viewBox="0 0 24 24" fill="none" stroke="#ee6524" stroke-width="2.4"><rect x="3" y="5" width="18" height="14" rx="1.5"/><path d="M3 6l9 7 9-7"/></svg>
        <span>info@corvane.com</span>
      </li>
      <li>
        <svg viewBox="0 0 24 24" fill="none" stroke="#ee6524" stroke-width="2.2"><circle cx="12" cy="12" r="9"/><path d="M3 12h18M12 3c3 3 3 15 0 18M12 3c-3 3-3 15 0 18"/></svg>
        <span>www.<b>corvane</b>.com</span>
      </li>
    </ul>
    <p class="address">Fenwick Lodge, Copse Lane<br>Ashcombe Vale, GU14 3TP</p>
  </div>
</section>

</body>
</html>
```